MRT Property - Business Cards

Looking for a business card & general letterhead, signage etc design for our new logo.

Colours:
000a20
0056a2
00b5ef
0088ce
68cef2

Fonts:
Poppins
Karla

Please keep look and feel of new brand - example in the zip package I sent.

```html
<!DOCTYPE html>
<html lang="en">
<head>
<meta charset="utf-8">
<title>MRT Property – Stationery</title>
<link href="https://fonts.googleapis.com/css2?family=Poppins:wght@400;600;700&family=Lato:wght@400;700&family=Parisienne&display=swap" rel="stylesheet">
<style>
  :root{
    --navy:#000a20;
    --card:#0b1222;
    --blue:#0056a2;
    --mid:#0088ce;
    --cyan:#00b5ef;
    --sky:#68cef2;
    --ink:#1a1a1a;
    --paper:#ffffff;
    --stage:#8a8a8a;
  }
  *{margin:0;padding:0;box-sizing:border-box}
  html,body{width:1200px;height:824px;overflow:hidden;background:var(--stage)}
  .board{position:relative;width:1200px;height:824px}

  .brand{font-family:"Poppins",sans-serif;font-weight:700;color:var(--blue);white-space:nowrap;line-height:1}
  .icon{display:inline-block;width:6px;height:6px;margin-right:2px;vertical-align:middle}

  /* Letterhead */
  .letterhead{position:absolute;left:127px;top:100px;width:441px;height:624px;background:var(--paper)}
  .letterhead .brand{position:absolute;left:22px;top:44px;font-size:33px}
  .letterhead .divider{position:absolute;left:294px;top:33px;width:1px;height:56px;background:var(--mid)}
  .letterhead .contact{position:absolute;left:319px;top:31px;font-family:"Poppins",sans-serif;font-size:8.4px;line-height:9.7px;color:var(--ink)}
  .letterhead .contact .address{margin-top:9px}
  .letter{position:absolute;left:22px;top:143px;width:398px;font-family:"Lato",sans-serif;font-size:9.2px;line-height:9.8px;color:var(--ink)}
  .letter p{margin-bottom:10px}
  .letter .date{margin-bottom:11px}
  .letter .salutation{font-weight:700;font-size:11.5px;margin:4px 0 12px}
  .letter .body{text-align:justify;margin-bottom:9px}
  .letter .closing{margin-top:23px}
  .letter .signature{font-family:"Parisienne",cursive;font-size:18px;margin-top:48px;line-height:1}

  /* Business cards */
  .card{position:absolute;top:100px;width:212px;height:121px;border-radius:11px;background:var(--card)}
  .card-front{left:632px}
  .card-back{left:860px}
  .card-front .brand{position:absolute;left:18px;top:56px;font-size:10.5px}
  .card-front .divider{position:absolute;left:113px;top:32px;width:1px;height:60px;background:var(--blue)}
  .card-details{position:absolute;left:121px;top:28px;font-family:"Poppins",sans-serif;color:#fff;font-size:5.8px;line-height:7.4px}
  .card-details .name{font-weight:700;font-size:8.6px;line-height:10px;color:var(--blue)}
  .card-details .gap{margin-top:4px}
  .card-back .brand{position:absolute;left:0;right:0;top:50px;text-align:center;font-size:22px}

  /* Envelope back */
  .envelope-back{position:absolute;left:622px;top:276px;width:451px;height:199px;background:var(--paper)}
  .envelope-back .flap{position:absolute;left:0;top:0;width:451px;height:58px;background:var(--card);border-radius:0 0 30px 30px}
  .envelope-back .brand{position:absolute;left:0;right:0;top:23px;text-align:center;font-size:12px;color:var(--cyan)}

  /* Envelope front */
  .envelope-front{position:absolute;left:622px;top:529px;width:451px;height:195px;background:var(--paper)}
  .envelope-front .brand{position:absolute;left:12px;top:22px;font-size:15px}
  .envelope-front .address{position:absolute;left:13px;top:71px;font-family:"Poppins",sans-serif;font-size:7.2px;line-height:8.6px;color:var(--ink)}
</style>
</head>
<body>
<div class="board">

  <section class="letterhead">
    <div class="brand">MRT Property</div>
    <div class="divider"></div>
    <div class="contact">
      <div><svg class="icon" viewBox="0 0 10 10"><path d="M2 1l2 2-1 1.5c.6 1.2 1.3 1.9 2.5 2.5L7 6l2 2-1.5 1.5C4 9 1 6 .5 2.5z" fill="var(--mid)"/></svg>123 456 789</div>
      <div><svg class="icon" viewBox="0 0 10 10"><rect x="1" y="2.5" width="8" height="5.5" rx="1" fill="var(--mid)"/></svg>info@mrtproperty.com</div>
      <div><svg class="icon" viewBox="0 0 10 10"><circle cx="5" cy="5" r="4" fill="var(--mid)"/></svg>www.mrtproperty.com</div>
      <div class="address">Your address, City<br>State, Zip 1234</div>
    </div>

    <div class="letter">
      <p class="date">January-03-2020</p>
      <p>Mr, Peter Lane<br>President</p>
      <p>Harbor Group<br>123 Street Name, Suite# 10<br>City, State, 120023</p>
      <p class="salutation">Dear Mr, Peter</p>
      <p class="body">Lorem ipsum dolor sit amet, consectetur adipiscing elit, sed do eiusmod tempor incididunt ut labore et dolore magna aliqua. Ut enim ad minim veniam, quis nostrud exercitation ullamco laboris nisi ut aliquip ex ea commodo consequat. Duis aute irure dolor in reprehenderit in voluptate velit esse cillum dolore eu fugiat nulla pariatur.</p>
      <p class="body">Lorem ipsum dolor sit amet, consectetur adipiscing elit, sed do eiusmod tempor incididunt ut labore et dolore magna aliqua. Ut enim ad minim veniam, quis nostrud exercitation ullamco laboris nisi ut aliquip ex ea commodo consequat. Duis aute irure dolor in reprehenderit in voluptate velit esse cillum dolore eu fugiat nulla pariatur.</p>
      <p class="body">Lorem ipsum dolor sit amet, consectetur adipiscing elit, sed do eiusmod tempor incididunt ut labore et dolore magna aliqua. Ut enim ad minim veniam, quis nostrud exercitation ullamco laboris nisi ut aliquip ex ea commodo consequat.</p>
      <p class="body">Excepteur sint occaecat cupidatat non proident, sunt in culpa qui officia deserunt mollit anim id est laborum. re et dolore magnam aliquam quaerat voluptatem.</p>
      <p class="closing">Regards</p>
      <p class="signature">Laura Bennett</p>
    </div>
  </section>

  <section class="card card-front">
    <div class="brand">MRT Property</div>
    <div class="divider"></div>
    <div class="card-details">
      <div class="name">DANIEL REYES</div>
      <div>Managing Director</div>
      <div class="gap">Your address, City<br>State, Zip 1234</div>
      <div class="gap"><svg class="icon" viewBox="0 0 10 10"><path d="M2 1l2 2-1 1.5c.6 1.2 1.3 1.9 2.5 2.5L7 6l2 2-1.5 1.5C4 9 1 6 .5 2.5z" fill="var(--cyan)"/></svg>123 456 789</div>
      <div><svg class="icon" viewBox="0 0 10 10"><rect x="1" y="2.5" width="8" height="5.5" rx="1" fill="var(--cyan)"/></svg>info@mrtproperty.com</div>
      <div><svg class="icon" viewBox="0 0 10 10"><circle cx="5" cy="5" r="4" fill="var(--cyan)"/></svg>www.mrtproperty.com</div>
    </div>
  </section>

  <section class="card card-back">
    <div class="brand">MRT Property</div>
  </section>

  <section class="envelope-back">
    <div class="flap"><div class="brand">MRT Property</div></div>
  </section>

  <section class="envelope-front">
    <div class="brand">MRT Property</div>
    <div class="address">Your address, City<br>State, Zip 1234</div>
  </section>

</div>
</body>
</html>
```